STOREFRONT LIT SIGN for The Cantera Workshop

A sign advertising our music academy. This sign will be hung 10 feet above the entrance of our building and will be seen by all pedestrian and vehicle traffic on Fenwick Lane Delano.

Target Market(s)

Street passerby

Industry/Entity Type

Music Training

Font styles to use
Other font styles liked:
• Creative

Colors

Designer to choose colors to be used in the design.

Requirements
Must have
• A White Background
• Dimensions: 8 ft long x 3 ft tall
• The Cantera Workshop of Delano
• Lecciones de Piano, Violin, Guitarra, Voz, Trompeta y Mas
• MUSIC ACADEMY *(This should be most prominent)
• Guitar, Voice, Trumpet and More
• (555) 384-7291
• thecanteraworkshop.example
Nice to have
• Graphics of a piano, or guitar, or violin or trumpet or a combination of two or more

```html
<!DOCTYPE html>
<html lang="en">
<head>
<meta charset="utf-8">
<title>The Cantera Workshop – Storefront Sign</title>
<link rel="stylesheet" href="https://fonts.googleapis.com/css2?family=Oswald:wght@600&family=Montserrat:wght@800&family=Poppins:wght@600;700&display=swap">
<style>
  :root{
    --backdrop:#eceef0;
    --sign-white:#ffffff;
    --sign-mist:#e3e6ea;
    --title-blue-dark:#16346b;
    --title-blue-light:#2373b8;
    --accent-red:#d40b0b;
    --ink:#111111;
    --contact-gray:#383838;
  }
  *{margin:0;padding:0;box-sizing:border-box}
  html,body{width:1200px;height:581px;overflow:hidden;background:var(--backdrop)}
  .sign{
    position:absolute;left:74px;top:74px;width:1054px;height:397px;
    background:
      linear-gradient(165deg,transparent 55%,rgba(210,214,220,.45) 56%,transparent 75%),
      linear-gradient(180deg,var(--sign-white) 0%,var(--sign-mist) 60%,var(--sign-white) 100%);
    overflow:hidden;
  }
  .violin-art{
    position:absolute;left:6px;top:4px;width:104px;height:388px;
    background:radial-gradient(ellipse at 50% 70%,#c9c9c9 0%,#e4e4e4 60%,transparent 75%);
    border-radius:40% 40% 45% 45%;
  }
  .clef-art{
    position:absolute;left:934px;top:10px;width:116px;height:376px;
    background:linear-gradient(180deg,#6d6d6d,#b4b4b4);
    border-radius:50% 50% 40% 40%;
    opacity:.55;
  }
  .content{position:absolute;left:100px;width:840px;text-align:center;white-space:nowrap}
  .studio-name{
    top:30px;
    font:600 80px/1.05 'Oswald',sans-serif;
    text-transform:uppercase;
    background:linear-gradient(180deg,var(--title-blue-light),var(--title-blue-dark));
    -webkit-background-clip:text;background-clip:text;color:transparent;
  }
  .academy{
    top:140px;
    font:800 56px/1 'Montserrat',sans-serif;
    letter-spacing:.22em;text-indent:.22em;
    color:var(--accent-red);
  }
  .lessons-es{
    top:220px;
    font:600 21px/1 'Poppins',sans-serif;
    color:var(--ink);
  }
  .lessons-en{
    top:266px;
    font:700 40px/1 'Poppins',sans-serif;
    color:var(--accent-red);
  }
  .divider{position:absolute;left:455px;top:331px;width:131px;height:2px;background:var(--accent-red)}
  .contact{
    top:347px;display:flex;justify-content:center;align-items:center;gap:18px;
    font:700 28px/1 'Poppins',sans-serif;color:var(--contact-gray);
  }
  .contact-item{display:flex;align-items:center;gap:10px;white-space:nowrap}
  .contact-item svg{width:24px;height:24px;flex:none}
  .website{font-size:24px}
</style>
</head>
<body>
  <div class="sign">
    <div class="violin-art" role="img" aria-label="Violin silhouette formed from scattered music notes"></div>
    <div class="clef-art" role="img" aria-label="Treble clef drawn with curving piano keys"></div>

    <h1 class="content studio-name">The Cantera Workshop</h1>
    <p class="content academy">MUSIC ACADEMY</p>
    <p class="content lessons-es">LECCIONES DE PIANO, VIOLIN, GUITARRA, VOZ, TROMPETA Y MAS</p>
    <p class="content lessons-en">GUITAR, VOICE, TRUMPET AND MORE</p>
    <div class="divider"></div>

    <div class="content contact">
      <span class="contact-item">
        <svg viewBox="0 0 24 24" aria-hidden="true">
          <circle cx="12" cy="12" r="12" fill="var(--accent-red)"/>
          <path d="M9 6.5c.6 0 1.2 1.9 1.2 2.4s-.9.9-.9 1.3c0 1.2 2 3.6 3.3 3.9.4.1.8-.9 1.3-.9s2.4 1 2.4 1.5c0 1-1.1 2.3-2.2 2.3-2.9 0-6.6-4-6.6-7 0-1.4 1-3.5 1.5-3.5z" fill="#fff"/>
        </svg>
        (555)&nbsp;384-7291
      </span>
      <span class="contact-item website">
        <svg viewBox="0 0 24 24" aria-hidden="true" fill="none" stroke="var(--accent-red)" stroke-width="2">
          <circle cx="12" cy="12" r="10"/>
          <ellipse cx="12" cy="12" rx="4.5" ry="10"/>
          <path d="M2 12h20M4 6.5h16M4 17.5h16"/>
        </svg>
        WWW.THECANTERAWORKSHOP.EXAMPLE
      </span>
    </div>
  </div>
</body>
</html>
```